New, modern business card for growing audiology practice

We need a new business card for our audiology practice. Our logo and website have recently changed (more modern) and we want our business cards to reflect this change.
We conduct hearing tests, perform earwax removals, and fit & dispense hearing aids to our patients. We are a family owned practice in which the owner is the one who works directly with the patient. I have attached logos in various formats to use, as well as two ideas I found on this website; as well as a scanned copy of our current logo. Good luck!

Industry/Entity Type

Business

Contact Information for Business Card

Company name: Tolvera Hearing Center
Provider name: Peter Wolstenby, Au.D. F/NSB
Phone number: (440) 683-5127
Address: 837 W. Lindell Ave. Brenford Vale, OH 44318
email: tolverahearing@postvane.com
website: tolverahearing.com

Colors
000000
aaaaaa
dbdbdb
cacaca
9bcb3c
afd23c
cadf82
b1b1b1

Requirements
Must have
• My card must include information in the "details" section. In the attached images, I found a few that I liked and I would like to model after - "brisky bouncin'" and "Sound Method Center".
• Must be horizontal.
• Must include logos provided. I uploaded them in various file formats and various ways.
• Must match logo font, if possible, if not, please get as close as you can.
Nice to have
• I really like the idea of having a color on one side with just the logo and company name and the contact information and provider name on the other side. I also really like the idea of having the main color dominating on the logo/company side with accent of that same color on the contact side of the card.
Should not have
• Must not be vertical.

```html
<!DOCTYPE html>
<html lang="en">
<head>
<meta charset="utf-8">
<title>Tolvera Hearing Center – Business Card</title>
<link rel="stylesheet" href="https://fonts.googleapis.com/css2?family=Lato:wght@400&family=Roboto:wght@400&family=Roboto+Condensed:wght@400;700&display=swap">
<style>
  :root {
    --backdrop: #d9d6d2;
    --card-white: #f3f3f3;
    --brand-green: #6f9e34;
    --accent-green: #9bcb3c;
    --ink-black: #000000;
    --text-white: #ffffff;
    --text-dark: #1a1a1a;
  }
  * { margin: 0; padding: 0; box-sizing: border-box; }
  html, body { width: 1200px; height: 960px; overflow: hidden; }
  body { background: var(--backdrop); position: relative; }

  .card {
    position: absolute;
    width: 600px;
    height: 343px;
    overflow: hidden;
    box-shadow: 0 3px 8px rgba(0,0,0,0.35);
  }
  .card--front { left: 314px; top: 113px; background: var(--card-white); }
  .card--back  { left: 311px; top: 472px; background: var(--ink-black); }

  .card__swoosh { position: absolute; inset: 0; }

  .brand {
    position: absolute;
    display: flex;
    align-items: center;
    font-family: "Lato", "Gill Sans", sans-serif;
    font-weight: 400;
    text-transform: uppercase;
    white-space: nowrap;
  }
  .brand__dot { border-radius: 50%; background: var(--brand-green); flex: none; }
  .brand--front { left: 40px; top: 92px; font-size: 19px; color: var(--text-dark); }
  .brand--front .brand__dot { width: 18px; height: 18px; margin-right: 10px; }
  .brand--back { left: 0; right: 0; top: 156px; justify-content: center; font-size: 29px; color: var(--text-white); }
  .brand--back .brand__dot { width: 26px; height: 26px; margin-right: 14px; }

  .contact {
    position: absolute;
    right: 24px;
    top: 163px;
    text-align: right;
    color: var(--text-white);
    font-family: "Roboto", Arial, sans-serif;
    font-size: 14.5px;
    line-height: 19px;
  }
  .contact__name {
    font-family: "Roboto Condensed", "Arial Narrow", sans-serif;
    font-weight: 700;
    font-size: 21px;
    line-height: 24px;
  }
  .contact__title {
    font-family: "Roboto Condensed", "Arial Narrow", sans-serif;
    font-weight: 400;
    font-size: 17px;
    line-height: 22px;
    margin-bottom: 8px;
  }
  .contact__address { margin-bottom: 8px; }
  .contact__line { display: flex; justify-content: flex-end; align-items: center; gap: 5px; }
  .contact__icon { width: 13px; height: 13px; fill: var(--text-white); flex: none; }

  .site {
    position: absolute;
    left: 0; right: 0; top: 288px;
    text-align: center;
    font-family: "Roboto", Arial, sans-serif;
    font-size: 14px;
    letter-spacing: 3.4px;
    color: var(--text-white);
  }
  .site__domain { color: var(--accent-green); }
</style>
</head>
<body>

  <section class="card card--front" aria-label="Business card front">
    <svg class="card__swoosh" viewBox="0 0 600 343" aria-hidden="true">
      <path d="M426 0 C470 45 470 150 130 343 L140 343 C500 150 500 45 467 0 Z" fill="var(--ink-black)"/>
      <path d="M146 343 C505 150 505 40 477 0 L600 0 L600 343 Z" fill="var(--brand-green)"/>
    </svg>

    <div class="brand brand--front">
      <span class="brand__dot"></span>Tolvera Hearing Center
    </div>

    <div class="contact">
      <div class="contact__name">PETER WOLSTENBY</div>
      <div class="contact__title">AU.D. F/NSB</div>
      <div class="contact__address">837 W. Lindell Ave.<br>Brenford Vale, OH 44318</div>
      <div class="contact__line">(440) 683-5127
        <svg class="contact__icon" viewBox="0 0 24 24" aria-hidden="true"><path d="M6.6 10.8a15.1 15.1 0 0 0 6.6 6.6l2.2-2.2c.3-.3.7-.4 1-.2 1.1.4 2.3.6 3.6.6.6 0 1 .4 1 1V20c0 .6-.4 1-1 1A17 17 0 0 1 3 4c0-.6.4-1 1-1h3.5c.6 0 1 .4 1 1 0 1.3.2 2.5.6 3.6.1.3 0 .7-.2 1z"/></svg>
      </div>
      <div class="contact__line">tolverahearing@postvane.com
        <svg class="contact__icon" viewBox="0 0 24 24" aria-hidden="true"><path d="M2 5h20v2l-10 6L2 7z"/><path d="M2 9l10 6 10-6v10H2z"/></svg>
      </div>
      <div class="contact__line">tolverahearing.com
        <svg class="contact__icon" viewBox="0 0 24 24" aria-hidden="true"><circle cx="12" cy="12" r="10"/><path d="M2 12h20M12 2c3 3 3 17 0 20M12 2c-3 3-3 17 0 20" fill="none" stroke="var(--brand-green)" stroke-width="1.6"/></svg>
      </div>
    </div>
  </section>

  <section class="card card--back" aria-label="Business card back">
    <div class="brand brand--back">
      <span class="brand__dot"></span>Tolvera Hearing Center
    </div>
    <div class="site">www.<span class="site__domain">tolverahearing</span>.com</div>
  </section>

</body>
</html>
```